Veterinary Pylon

My veterinary clinic is not clearly visible from the street and I want to place a Pylon next to my driveway. I want a modern, elegant straight Design, the Photo shows the sheduled place. One can see the clinic on our Homepage: www.tailbright-vethaus.at
The last pictures are examples for pylones I like

Target Market(s)

the passing cars often miss my entry...I want to show where to turn left

Colors
3276b5
33a6d7
00a990

Requirements
Must have
• High value, simple elegance, size: 250cm (high) x 100cm (width)
Nice to have
• Our Logo, arrow(?)

A special Text is not necessary but this will be an option:

Biegen sie hier ab und wir biegen es wieder hin!
Should not have
• Too much Color, the colors I have chosen are the possible colors but it‘s not necessary to use them.

```html
<!DOCTYPE html>
<html lang="de">
<head>
<meta charset="utf-8">
<title>Tailbright Vethaus – Pylon</title>
<link href="https://fonts.googleapis.com/css2?family=Archivo+Black&display=swap" rel="stylesheet">
<style>
  :root {
    --navy: #124b92;
    --cyan: #2fbadd;
    --mist-top: #f4fdfe;
    --mist-bottom: #dff2f8;
    --white: #ffffff;
  }
  html, body {
    margin: 0;
    padding: 0;
    width: 1200px;
    height: 3000px;
    overflow: hidden;
    background: var(--white);
  }
  .pylon {
    position: relative;
    width: 1200px;
    height: 3000px;
    overflow: hidden;
    background: var(--white);
  }
  .pylon__shapes {
    position: absolute;
    inset: 0;
    width: 1200px;
    height: 3000px;
  }
  .brand {
    position: absolute;
    left: 0;
    top: 470px;
    width: 1200px;
    margin: 0;
    text-align: center;
    font-family: "Archivo Black", sans-serif;
    font-weight: 400;
    color: var(--navy);
    text-transform: uppercase;
    line-height: 1.05;
  }
  .brand__line {
    display: block;
    font-size: 124px;
    letter-spacing: 2px;
  }
</style>
</head>
<body>
<main class="pylon">
  <svg class="pylon__shapes" viewBox="0 0 1200 3000" xmlns="http://www.w3.org/2000/svg" aria-hidden="true">
    <defs>
      <linearGradient id="turn-gradient" x1="0" y1="0" x2="1" y2="0">
        <stop offset="0" stop-color="var(--navy)" style="stop-color:#124b92"/>
        <stop offset="1" stop-color="var(--cyan)" style="stop-color:#2fbadd"/>
      </linearGradient>
    </defs>

    <!-- header field -->
    <path class="header-field" d="M0 0 H1200 V1031 Q600 1292 0 996 Z" fill="#f4fdfe"/>
    <!-- header swoosh -->
    <path class="header-swoosh" d="M123 1080 Q638 1332 1153 1080 Q638 1284 123 1080 Z" fill="#2fbadd"/>

    <!-- turn-left sign -->
    <g class="turn-sign">
      <circle cx="584" cy="1695" r="212" fill="url(#turn-gradient)"/>
      <path d="M557 1599 L461 1695 L557 1791 M461 1695 H708" fill="none" stroke="#ffffff" stroke-width="21" stroke-linejoin="miter" stroke-miterlimit="10"/>
    </g>

    <!-- footer swoosh -->
    <path class="footer-swoosh" d="M123 2262 Q638 2008 1153 2262 Q638 2058 123 2262 Z" fill="#2fbadd"/>
    <!-- footer field -->
    <path class="footer-field" d="M0 2336 Q600 2038 1200 2300 V3000 H0 Z" fill="#dff2f8"/>
  </svg>

  <h1 class="brand">
    <span class="brand__line">Tailbright</span>
    <span class="brand__line">Vethaus</span>
  </h1>
</main>
</body>
</html>
```